Website Design for a Chemical Sales Company

We are working with a Chemical Sales Company in California. They sell various chemicals throughout the US.
Types of products they sell: https://www.wardenvale.example/us/products/all
https://www.molvista.example/products/kerrin/glacyn-glycol-thermal-fluids/glacyn-propylene-glycol-thermal-fluids
Some sites to use for inspiration:
https://www.molvista.example
https://www.kerrin.example/en-us
Thank you for taking the time to consider designing a website for us. We are web developers based in Stockton, CA, USA. Most of our projects go through the same process. Understanding this process may help you win a project with us. We custom-code all of our websites in-house. We don’t have any requirements as to what tools you use for your design, but we ask that you follow these guidelines.
IMAGES:
If you use any images or icons in the design, we ask that you have a link to the asset so we can purchase the image/icon. Most of the designs we submit do not have the customer’s images on them unless they have some great images. Be creative; show us the feeling you are trying to portray with your image choices. Use any royalty-free site you choose. We subscribe to Pelmora and mainly use their images, but we can purchase images outside of Pelmora. PLEASE NOTE: we will not submit designs to clients with watermarks on the images.
FONTS:
We ask that you identify the fonts you’re using in the design. This can be done in a message if you want. We typically use Google Fonts and Pelmora Fonts.
CONTENT:
We're always open to different content and ideas. We often submit designs with stock images so the client can see our vision. We typically take pictures after the website launch to use their images with our vision. Lorem Ipsum is fine for paragraphs, but we ask that you make the Headers with correct English. We want to be able to show the vision and identify the sections of the website.
INSPIRATION:
We typically add a couple of links in the brief of websites we like to help you get started in your design.
REVISIONS:
We do not often ask for revisions of the designs unless we see something in the design that may not appeal to the client. If there are slight changes that we want to make, we do that in the development process.
FEEDBACK:
We rarely give feedback on designs during the design process. We are working on many website projects and do not have the time to provide feedback. We usually respond if your request is well thought out and asks specific questions, but a note asking “feedback, please” usually goes unanswered.

```html
<!DOCTYPE html>
<html lang="en">
<head>
<meta charset="utf-8">
<title>Ionwell — Chemical Sales</title>
<link href="https://fonts.googleapis.com/css2?family=Barlow+Condensed:wght@400;500;600&family=Outfit:wght@300;400;500;600&display=swap" rel="stylesheet">
<style>
:root{
  --blue:#0aa4e0;
  --blue-bar:#27ade3;
  --ink:#1d1d1f;
  --text:#3a3a3a;
  --grey:#efefef;
  --white:#fff;
  --quote:#7cd0f0;
}
*{margin:0;padding:0;box-sizing:border-box}
html,body{width:1200px;height:4249px;overflow:hidden}
body{position:relative;background:var(--white);font-family:'Outfit',sans-serif;color:var(--text)}
.abs{position:absolute}
.heading{font-family:'Barlow Condensed',sans-serif;font-weight:400;color:var(--ink);text-align:center;position:absolute;left:0;width:1200px}
.btn{position:absolute;background:var(--blue);color:var(--white);border-radius:22px;font-size:18px;display:flex;align-items:center;justify-content:center}
.arrow-dot{position:absolute;width:40px;height:40px;border-radius:50%;background:var(--blue);border:3px solid var(--white);display:flex;align-items:center;justify-content:center;z-index:2}

/* header */
.site-header{position:absolute;left:0;top:0;width:1200px;height:113px;background:var(--white)}
.brand{position:absolute;left:113px;top:46px;display:flex;align-items:center;gap:10px;font-size:20px;color:var(--ink);letter-spacing:1px}
.brand .dot{width:12px;height:12px;border-radius:50%;background:var(--blue)}
.nav a{position:absolute;top:49px;font-size:15px;color:var(--text);text-decoration:none}
.nav .active{border-bottom:2px solid var(--blue);padding-bottom:2px}
.phone-btn{left:921px;top:36px;width:193px;height:42px;font-size:17px;gap:8px}

/* hero */
.hero{position:absolute;left:0;top:113px;width:1200px;height:622px;overflow:hidden}
.hero-media{position:absolute;inset:0;background:
  radial-gradient(circle at 18% 62%,rgba(255,255,255,.35) 0,transparent 22%),
  radial-gradient(circle at 70% 50%,rgba(255,255,255,.3) 0,transparent 18%),
  radial-gradient(circle at 92% 15%,rgba(200,240,245,.55) 0,transparent 16%),
  radial-gradient(circle at 14% 10%,#f59a1a 0,#ea5a24 20%,transparent 42%),
  radial-gradient(circle at 30% 45%,#e25a30 0,transparent 30%),
  radial-gradient(circle at 60% 80%,#9ec2c4 0,transparent 35%),
  radial-gradient(circle at 88% 62%,#13a3ae 0,transparent 45%),
  linear-gradient(100deg,#e8602a 0%,#d4795a 28%,#b9aaa6 48%,#6fbfc4 68%,#1c9cab 100%)}
.hero-title-small{position:absolute;top:186px;left:0;width:1200px;text-align:center;font-family:'Barlow Condensed',sans-serif;font-size:44px;color:var(--white)}
.hero-title{position:absolute;top:224px;left:0;width:1200px;text-align:center;font-family:'Barlow Condensed',sans-serif;font-size:76px;font-weight:400;color:var(--white)}
.hero-btn{left:520px;top:332px;width:160px;height:41px}
.hero-edge{position:absolute;left:0;bottom:0}

/* products */
.product-card{position:absolute;width:211px;height:335px;background:var(--white);border-radius:8px;box-shadow:0 3px 12px rgba(0,0,0,.14);text-align:center}
.product-card .pack{position:absolute;left:50px;top:22px;width:111px;height:150px;border-radius:12px 12px 8px 8px;box-shadow:inset -10px 0 14px rgba(0,0,0,.12),inset 8px 0 10px rgba(255,255,255,.35),0 6px 10px rgba(0,0,0,.12)}
.product-card .pack.tube{left:86px;width:40px;border-radius:6px}
.product-card h3{position:absolute;top:196px;left:0;width:211px;font-size:17px;font-weight:600;color:var(--ink);line-height:27px;text-transform:uppercase}
.product-card p{position:absolute;top:268px;left:20px;width:171px;font-size:14px;font-weight:300;line-height:25px}
.product-card .arrow-dot{right:-4px;bottom:-12px}

/* partners */
.partners{position:absolute;left:0;top:1916px;width:1200px;height:440px;background:var(--grey)}
.partner-mark{position:absolute;top:2085px;width:76px;height:76px}

/* blog */
.blog-media{position:absolute;border-radius:10px;overflow:hidden}
.blog-lead h3{position:absolute;left:64px;top:2953px;font-size:31px;font-weight:300;color:var(--ink)}
.blog-lead p{position:absolute;left:64px;top:3002px;width:500px;font-size:16px;font-weight:300;line-height:29px}
.blog-item h3{position:absolute;left:880px;font-size:31px;font-weight:300;color:var(--ink)}
.blog-item p{position:absolute;left:880px;width:280px;font-size:15px;font-weight:300;line-height:29px}

/* testimonials */
.testimonials{position:absolute;left:0;top:3312px;width:1200px;height:520px;background:var(--grey)}
.quote-mark{position:absolute;left:208px;top:3385px}
.testimonial-card{position:absolute;left:246px;top:3455px;width:708px;height:243px;background:var(--white);border-radius:16px;text-align:center}
.testimonial-card h4{margin-top:40px;font-size:22px;font-weight:400;color:var(--ink)}
.testimonial-card .stars{margin-top:4px;display:flex;justify-content:center}
.testimonial-card p{margin:14px auto 0;width:620px;font-size:16px;font-weight:300;line-height:29px}
.slider-arrow{position:absolute;top:3563px}

/* footer */
.site-footer{position:absolute;left:0;top:3740px;width:1200px;height:509px}
.foot-brand{position:absolute;left:113px;top:3960px;display:flex;align-items:center;gap:10px;font-size:20px;color:var(--white);letter-spacing:1px}
.foot-brand .dot{width:12px;height:12px;border-radius:50%;background:var(--white)}
.foot-col{position:absolute;top:3940px;color:var(--white)}
.foot-col h5{font-size:17px;font-weight:600;margin-bottom:6px}
.foot-col a{display:block;font-size:16px;font-weight:300;line-height:29px;color:var(--white);text-decoration:none}
.contact-line{position:absolute;left:113px;color:var(--white);font-size:15px;font-weight:300;display:flex;align-items:center;gap:8px}
.newsletter-input{position:absolute;left:805px;top:3985px;width:283px;height:48px;background:var(--white);border-radius:6px;font-size:15px;color:#999;padding:15px 16px}
.newsletter-note{position:absolute;left:808px;top:4048px;width:270px;font-size:14px;font-weight:300;line-height:28px;color:var(--white)}
.copyright-bar{position:absolute;left:0;top:4184px;width:1200px;height:65px;background:var(--blue-bar);color:var(--white);font-size:14px;font-weight:300;display:flex;align-items:center;justify-content:center}
</style>
</head>
<body>

<header class="site-header">
  <div class="brand"><span class="dot"></span>IONWELL</div>
  <nav class="nav">
    <a class="active" style="left:434px">Home</a>
    <a style="left:520px">About Us</a>
    <a style="left:626px">Products</a>
    <a style="left:731px">Support</a>
    <a style="left:830px">Contact</a>
  </nav>
  <div class="btn phone-btn">
    <svg width="14" height="14" viewBox="0 0 24 24" fill="#fff"><path d="M6.6 10.8a15.1 15.1 0 0 0 6.6 6.6l2.2-2.2a1 1 0 0 1 1-.25 11.4 11.4 0 0 0 3.6.57 1 1 0 0 1 1 1V20a1 1 0 0 1-1 1A17 17 0 0 1 3 4a1 1 0 0 1 1-1h3.5a1 1 0 0 1 1 1c0 1.25.2 2.45.57 3.6a1 1 0 0 1-.25 1z"/></svg>
    +1 555 014 2290
  </div>
</header>

<section class="hero">
  <div class="hero-media" role="img" aria-label="Close-up of colourful oil bubbles in liquid, orange to teal"></div>
  <div class="hero-title-small">Welcome To</div>
  <h1 class="hero-title">Ionwell</h1>
  <div class="btn hero-btn">Get Started</div>
  <svg class="hero-edge" width="1200" height="130" viewBox="0 0 1200 130">
    <polygon points="0,96 528,52 790,120 1200,118 1200,130 0,130" fill="#fff"/>
    <polygon points="0,78 528,34 800,110 1200,104 1200,118 790,120 528,52 0,96" fill="#0aa4e0"/>
  </svg>
</section>

<h2 class="heading" style="top:830px;font-size:38px">Our Products</h2>

<div class="product-card" style="left:118px;top:943px">
  <div class="pack" role="img" aria-label="White thermal fluid container with red label" style="background:linear-gradient(180deg,#fafafa 0,#f0f0f0 22%,#e04040 22%,#d8343a 58%,#f4f4f4 58%,#e2e2e2 100%)"></div>
  <h3>K100 Solar<br>Thermal Fluid</h3><p>Lorem ipsum dolor sit amet, consectetur</p>
  <div class="arrow-dot"><svg width="18" height="18" viewBox="0 0 24 24" fill="none" stroke="#fff" stroke-width="2"><path d="M4 12h15M13 6l6 6-6 6"/></svg></div>
</div>
<div class="product-card" style="left:370px;top:943px">
  <div class="pack" role="img" aria-label="Two white cleaner containers with blue labels" style="background:linear-gradient(180deg,#fafafa 0,#f1f1f1 35%,#7e93c4 35%,#5d78b8 62%,#f1f1f1 62%,#dedede 100%)"></div>
  <h3>K200 Solar<br>Cleaner</h3><p>Lorem ipsum dolor sit amet, consectetur</p>
  <div class="arrow-dot"><svg width="18" height="18" viewBox="0 0 24 24" fill="none" stroke="#fff" stroke-width="2"><path d="M4 12h15M13 6l6 6-6 6"/></svg></div>
</div>
<div class="product-card" style="left:621px;top:943px">
  <div class="pack" role="img" aria-label="Teal cleaner container with red label" style="background:linear-gradient(180deg,#8fe2e2 0,#5fd0d2 30%,#e04848 30%,#cc2f36 60%,#4cc4c8 60%,#2fb0b6 100%)"></div>
  <h3>Wardenvale V400<br>Cleaner</h3><p>Lorem ipsum dolor sit amet, consectetur</p>
  <div class="arrow-dot"><svg width="18" height="18" viewBox="0 0 24 24" fill="none" stroke="#fff" stroke-width="2"><path d="M4 12h15M13 6l6 6-6 6"/></svg></div>
</div>
<div class="product-card" style="left:872px;top:943px">
  <div class="pack" role="img" aria-label="Yellow inhibitor container with red label" style="background:linear-gradient(180deg,#ffec70 0,#ffe040 30%,#e84040 30%,#d42c30 60%,#f7d21e 60%,#efc000 100%)"></div>
  <h3>K100 Solar<br>Thermal Fluid</h3><p>Lorem ipsum dolor sit amet, consectetur</p>
  <div class="arrow-dot"><svg width="18" height="18" viewBox="0 0 24 24" fill="none" stroke="#fff" stroke-width="2"><path d="M4 12h15M13 6l6 6-6 6"/></svg></div>
</div>

<div class="product-card" style="left:118px;top:1343px">
  <div class="pack tube" role="img" aria-label="Yellow dosing cartridge with red cap" style="background:linear-gradient(180deg,#e63030 0,#d42020 22%,#f8dc50 22%,#f2c82a 100%)"></div>
  <h3>V100 Inhibitor<br>Quick-Dose</h3><p>Lorem ipsum dolor sit amet, consectetur</p>
  <div class="arrow-dot"><svg width="18" height="18" viewBox="0 0 24 24" fill="none" stroke="#fff" stroke-width="2"><path d="M4 12h15M13 6l6 6-6 6"/></svg></div>
</div>
<div class="product-card" style="left:370px;top:1343px">
  <div class="pack" role="img" aria-label="Red noise reducer container" style="background:linear-gradient(180deg,#f6f6f6 0,#eaeaea 18%,#f25050 18%,#d91e1e 100%)"></div>
  <h3>V200 Noise<br>Reducer</h3><p>Lorem ipsum dolor sit amet, consectetur</p>
  <div class="arrow-dot"><svg width="18" height="18" viewBox="0 0 24 24" fill="none" stroke="#fff" stroke-width="2"><path d="M4 12h15M13 6l6 6-6 6"/></svg></div>
</div>
<div class="product-card" style="left:621px;top:1343px">
  <div class="pack" role="img" aria-label="Blue system cleaner container" style="background:linear-gradient(180deg,#f6f6f6 0,#eaeaea 18%,#d83a3a 18%,#c82c2c 30%,#3f84e6 30%,#1e5cc8 100%)"></div>
  <h3>V300 System<br>Cleaner</h3><p>Lorem ipsum dolor sit amet, consectetur</p>
  <div class="arrow-dot"><svg width="18" height="18" viewBox="0 0 24 24" fill="none" stroke="#fff" stroke-width="2"><path d="M4 12h15M13 6l6 6-6 6"/></svg></div>
</div>
<div class="product-card" style="left:872px;top:1343px">
  <div class="pack tube" role="img" aria-label="Light blue dosing cartridge with red cap" style="background:linear-gradient(180deg,#e63030 0,#d42020 22%,#e4f3fb 22%,#bfe2f4 100%)"></div>
  <h3>V400 Cleaner<br>Quick-Dose</h3><p>Lorem ipsum dolor sit amet, consectetur</p>
  <div class="arrow-dot"><svg width="18" height="18" viewBox="0 0 24 24" fill="none" stroke="#fff" stroke-width="2"><path d="M4 12h15M13 6l6 6-6 6"/></svg></div>
</div>

<div class="btn" style="left:520px;top:1773px;width:160px;height:41px">Read More</div>

<section class="partners">
  <svg class="abs" style="left:0;bottom:0" width="1200" height="100" viewBox="0 0 1200 100">
    <polygon points="0,60 527,2 800,100 0,100" fill="#fff"/>
    <polygon points="527,2 800,100 1200,100 1200,90" fill="#fff"/>
  </svg>
</section>
<h2 class="heading" style="top:1985px;font-size:38px">Proudly Partnered With</h2>
<div class="partner-mark" style="left:128px;border-radius:50%;background:linear-gradient(135deg,#f05a9a,#d8245e)"></div>
<div class="partner-mark" style="left:348px;border-radius:12px;background:linear-gradient(135deg,#4ab0cc,#1d7a98)"></div>
<div class="partner-mark" style="left:570px;border-radius:50%;background:linear-gradient(135deg,#3d6688,#1d3550)"></div>
<div class="partner-mark" style="left:786px;border-radius:12px;background:linear-gradient(135deg,#8a6cf0,#4a2fc0)"></div>
<div class="partner-mark" style="left:996px;border-radius:50%;background:linear-gradient(135deg,#c22a8a,#7e0f55)"></div>

<h2 class="heading" style="top:2437px;font-size:38px">Blog</h2>
<div class="blog-media" role="img" aria-label="Warehouse stacked with blue chemical drums on pallets" style="left:46px;top:2542px;width:549px;height:386px;background:
  radial-gradient(ellipse at 12% 55%,rgba(240,245,250,.75) 0,transparent 28%),
  linear-gradient(180deg,#a8b2ba 0,#7e8c98 22%,#2f66c4 40%,#1f52b2 70%,#c2a27a 86%,#1a3f8a 100%)"></div>
<div class="arrow-dot" style="left:552px;top:2900px"><svg width="18" height="18" viewBox="0 0 24 24" fill="none" stroke="#fff" stroke-width="2"><path d="M4 12h15M13 6l6 6-6 6"/></svg></div>
<div class="blog-lead">
  <h3>Ionwell Blog 1</h3>
  <p>Lorem ipsum dolor sit amet, consectetur adipiscing elit, sed do eiusmod tempor incididunt ut labore et dolore magna aliqua. Quis ipsum suspendisse ultrices gravida.</p>
</div>

<div class="blog-media" role="img" aria-label="Rows of blue drums on pallets" style="left:608px;top:2542px;width:249px;height:175px;background:
  linear-gradient(180deg,#b4bcc4 0,#8a98a6 18%,#2c62c0 34%,#1f50ae 62%,#b8976c 74%,#2256b6 84%,#1a3f8a 100%)"></div>
<div class="arrow-dot" style="left:822px;top:2680px"><svg width="18" height="18" viewBox="0 0 24 24" fill="none" stroke="#fff" stroke-width="2"><path d="M4 12h15M13 6l6 6-6 6"/></svg></div>
<div class="blog-item"><h3 style="top:2555px">Ionwell Blog 1</h3><p style="top:2605px">Lorem ipsum dolor sit amet, consectetur adipiscing elit, sed do eiusmod tempor incididunt ut</p></div>

<div class="blog-media" role="img" aria-label="Stacked white bulk liquid containers in a warehouse" style="left:608px;top:2731px;width:249px;height:175px;background:
  radial-gradient(ellipse at 75% 80%,rgba(200,90,70,.45) 0,transparent 30%),
  linear-gradient(180deg,#dfe3e6 0,#c4cace 30%,#eef0f1 45%,#a9b0b6 60%,#d6dadd 78%,#8e969c 100%)"></div>
<div class="arrow-dot" style="left:822px;top:2869px"><svg width="18" height="18" viewBox="0 0 24 24" fill="none" stroke="#fff" stroke-width="2"><path d="M4 12h15M13 6l6 6-6 6"/></svg></div>
<div class="blog-item"><h3 style="top:2744px">Ionwell Blog 1</h3><p style="top:2794px">Lorem ipsum dolor sit amet, consectetur adipiscing elit, sed do eiusmod tempor incididunt ut</p></div>

<div class="blog-media" role="img" aria-label="Chemical plant with steel tanks under blue sky" style="left:608px;top:2920px;width:249px;height:175px;background:
  radial-gradient(ellipse at 70% 15%,rgba(255,255,255,.7) 0,transparent 30%),
  linear-gradient(180deg,#5fa6dc 0,#a6cfeb 38%,#c8d0d6 52%,#8e9aa4 72%,#b4b8ba 86%,#6c747a 100%)"></div>
<div class="arrow-dot" style="left:822px;top:3058px"><svg width="18" height="18" viewBox="0 0 24 24" fill="none" stroke="#fff" stroke-width="2"><path d="M4 12h15M13 6l6 6-6 6"/></svg></div>
<div class="blog-item"><h3 style="top:2933px">Ionwell Blog 1</h3><p style="top:2983px">Lorem ipsum dolor sit amet, consectetur adipiscing elit, sed do eiusmod tempor incididunt ut</p></div>

<div class="btn" style="left:520px;top:3180px;width:160px;height:41px">Read More</div>

<section class="testimonials"></section>
<svg class="quote-mark" width="138" height="115" viewBox="0 0 138 115" fill="#7cd0f0">
  <path d="M8 115V50C8 20 24 4 56 0v22c-16 3-22 12-22 28h22v65z"/>
  <path d="M76 115V50C76 20 92 4 124 0v22c-16 3-22 12-22 28h22v65z"/>
</svg>
<h2 class="heading" style="top:3372px;font-size:38px">Testimonials</h2>
<div class="testimonial-card">
  <h4>Dana Whitfield</h4>
  <div class="stars">
    <svg width="110" height="20" viewBox="0 0 110 20" fill="#0aa4e0">
      <g id="s"><path d="M10 1l2.7 5.6 6.1.8-4.4 4.3 1 6.1L10 15l-5.4 2.8 1-6.1L1.2 7.4l6.1-.8z"/></g>
      <use href="#s" x="22"/><use href="#s" x="44"/><use href="#s" x="66"/><use href="#s" x="88"/>
    </svg>
  </div>
  <p>Lorem ipsum dolor sit amet, consectetur adipiscing elit, sed do eiusmod tempor incididunt ut labore et dolore magna aliqua. Quis ipsum suspendisse ultrices gravida. Risus commodo viverra maecenas accumsan lacus vel facilisis.</p>
</div>
<svg class="slider-arrow" style="left:196px" width="20" height="26" viewBox="0 0 20 26"><path d="M15 2L5 13l10 11" fill="none" stroke="#111" stroke-width="3"/></svg>
<svg class="slider-arrow" style="left:984px" width="20" height="26" viewBox="0 0 20 26"><path d="M5 2l10 11L5 24" fill="none" stroke="#111" stroke-width="3"/></svg>

<footer class="site-footer">
  <svg class="abs" style="left:0;top:0" width="1200" height="509" viewBox="0 0 1200 509">
    <polygon points="0,42 530,4 800,98 1200,98 1200,509 0,509" fill="#0aa4e0"/>
  </svg>
</footer>
<div class="foot-brand"><span class="dot"></span>IONWELL</div>
<div class="contact-line" style="top:4030px;font-weight:600;font-size:16px">Contact</div>
<div class="contact-line" style="top:4060px">
  <svg width="12" height="12" viewBox="0 0 24 24" fill="#fff"><path d="M6.6 10.8a15.1 15.1 0 0 0 6.6 6.6l2.2-2.2a1 1 0 0 1 1-.25 11.4 11.4 0 0 0 3.6.57 1 1 0 0 1 1 1V20a1 1 0 0 1-1 1A17 17 0 0 1 3 4a1 1 0 0 1 1-1h3.5a1 1 0 0 1 1 1c0 1.25.2 2.45.57 3.6a1 1 0 0 1-.25 1z"/></svg>(1) 555 014 229</div>
<div class="contact-line" style="top:4089px">
  <svg width="12" height="10" viewBox="0 0 24 20" fill="#fff"><path d="M2 2h20v16H2z M2 2l10 8 10-8" stroke="#0aa4e0" stroke-width="1.5"/></svg>info@ionwell.example</div>

<div class="foot-col" style="left:393px">
  <h5>Quick Links</h5><a>Home</a><a>About Us</a><a>Product</a><a>Support</a><a>Contact</a>
</div>
<div class="foot-col" style="left:581px">
  <h5>Help Links</h5><a>Support</a><a>Terms &amp; Conditions</a><a>Privacy Policy</a><a>FAQ</a>
</div>
<div class="foot-col" style="left:805px"><h5>Sign Up For Newsletter</h5></div>
<div class="newsletter-input">Email</div>
<svg class="abs" style="left:1050px;top:3999px" width="20" height="20" viewBox="0 0 24 24" fill="#0aa4e0"><path d="M2 21l21-9L2 3v7l15 2-15 2z"/></svg>
<p class="newsletter-note">Lorem ipsum dolor sit amet, elit, sed do eiusmod tempor incididunt.</p>

<div class="copyright-bar">© copyrights 2023 Ionwell | All Rights Reserved</div>

</body>
</html>
```